Venture 482 - Lumora Book Cover

I am looking for a Lumora book cover for my book about "Venture 482".
The Book is Titled:
Venture 482 Ascended
Shaping Outcomes: Paths To Unlocking Cosmic Truths
Author is Dorian Pell
Here is a book description that may help you understand more about it:
Inspired by the genius of Edwin Marlowe, this comprehensive guide delves into the ancient wisdom and cutting-edge science behind the 482 method, a powerful tool for manifesting your desires. Whether you're seeking personal growth, financial success, or spiritual enlightenment, this book provides advanced techniques and methods to transform your dreams into reality.
Any questions please ask.
Thanks
Owen

```html
<!DOCTYPE html>
<html lang="en">
<head>
<meta charset="utf-8">
<title>Venture 482 Ascended — Book Cover</title>
<link rel="stylesheet" href="https://fonts.googleapis.com/css2?family=Cinzel:wght@400;500&family=Tinos:wght@400;700&display=swap">
<style>
  :root {
    --backdrop: #e6e6e4;
    --sky-top: #2e2660;
    --sky-mid: #221a4c;
    --sky-bottom: #0e0923;
    --title-cream: #fbeee6;
    --band-cream: #fdfbe0;
    --band-ink: #3b2d6e;
    --numeral-teal: #4f93a8;
    --subtitle-white: #ffffff;
    --author-peach: #f1dfd4;
  }
  * { box-sizing: border-box; margin: 0; padding: 0; }
  html, body {
    width: 1200px;
    height: 1131px;
    overflow: hidden;
    background: var(--backdrop);
  }
  .book-cover {
    position: absolute;
    left: 246px;
    top: 30px;
    width: 708px;
    height: 1071px;
    overflow: hidden;
    text-align: center;
  }
  .night-sky {
    position: absolute;
    inset: 0;
    background:
      radial-gradient(ellipse 80% 40% at 30% 12%, rgba(120, 105, 190, 0.35), transparent 70%),
      linear-gradient(180deg, var(--sky-top) 0%, var(--sky-mid) 45%, var(--sky-bottom) 100%);
  }
  .numeral-ring {
    position: absolute;
    left: 0;
    top: 0;
    width: 708px;
    height: 1071px;
  }
  .title-block {
    position: absolute;
    left: 0;
    right: 0;
    top: 258px;
    color: var(--title-cream);
    font-family: "Cinzel", serif;
  }
  .title-word {
    display: block;
    font-size: 88px;
    font-weight: 400;
    line-height: 1;
    letter-spacing: -1px;
  }
  .title-number {
    display: block;
    font-size: 196px;
    font-weight: 400;
    line-height: 1;
    margin-top: 8px;
    letter-spacing: -4px;
  }
  .edition-band {
    position: absolute;
    left: 146px;
    top: 566px;
    width: 410px;
    height: 48px;
    background: var(--band-cream);
    color: var(--band-ink);
    font-family: "Tinos", serif;
    font-size: 30px;
    line-height: 48px;
    letter-spacing: 25px;
    padding-left: 25px;
  }
  .subtitle {
    position: absolute;
    left: 0;
    right: 0;
    top: 840px;
    color: var(--subtitle-white);
    font-family: "Tinos", serif;
    font-size: 23px;
    line-height: 1.22;
  }
  .subtitle-lead {
    display: block;
    font-weight: 700;
    font-size: 25px;
    letter-spacing: -0.5px;
  }
  .author {
    position: absolute;
    left: 0;
    right: 0;
    top: 988px;
    color: var(--author-peach);
    font-family: "Cinzel", serif;
    font-size: 38px;
    letter-spacing: 13px;
    padding-left: 13px;
  }
</style>
</head>
<body>
  <main class="book-cover">
    <div class="night-sky" role="img" aria-label="Starry night sky with a faint constellation"></div>

    <svg class="numeral-ring" viewBox="0 0 708 1071" role="img" aria-label="Swirling ring of scattered hand-drawn numerals">
      <defs>
        <radialGradient id="ring-glow" cx="340" cy="462" r="330" gradientUnits="userSpaceOnUse">
          <stop offset="0.72" stop-color="#4f93a8" stop-opacity="0"/>
          <stop offset="0.86" stop-color="#4f93a8" stop-opacity="0.4"/>
          <stop offset="1" stop-color="#4f93a8" stop-opacity="0"/>
        </radialGradient>
      </defs>
      <ellipse cx="340" cy="462" rx="320" ry="332" fill="url(#ring-glow)"/>
    </svg>

    <h1 class="title-block">
      <span class="title-word">VENTURE</span>
      <span class="title-number">482</span>
    </h1>

    <p class="edition-band">ASCENDED</p>

    <p class="subtitle">
      <span class="subtitle-lead">SHAPING OUTCOMES:</span>
      Paths to unlocking<br>cosmic truths
    </p>

    <p class="author">DORIAN PELL</p>
  </main>
</body>
</html>
```